Cool date project and tattoo

My children were born randomly on dates with a crazy number sequence and I am getting married on the next date in the sequence. The dates are as follows:

6/13/14
7/15/16
8/17/18
9/19/20.

I want a piece of art that has these dates beautifully drawn/written which I also would like to turn into a tattoo one day. I am not sure whether to add the kids names or not but would also be interested in seeing options. Here are the names of the kids and the wedding:

6/13/14 - Colby
7/15/16 - Fenna
8/17/18 - Mireth
9/19/20 - Wedding

I'd love to see options of how these dates could be presented in a unique and beautiful way!

I have not seen anything that I love yet..

Serif
Decorative
Script

• My project must have the dates included in the design
• I want to be able to see the dates relatively clearly, I want it to be able to not only be a large art project when printed on a large canvas, but also a cool looking tattoo.

Please check the color palates I added to see colors I like together.

```html
<!DOCTYPE html>
<html lang="en">
<head>
<meta charset="utf-8">
<title>Date Sequence Print</title>
<link href="https://fonts.googleapis.com/css2?family=Young+Serif&display=swap" rel="stylesheet">
<style>
  :root {
    --page: #efeeea;
    --paper: #e8e3d6;
    --ink: #6b2a16;
    --ornament: rgba(107, 42, 22, 0.35);
  }
  * { margin: 0; padding: 0; box-sizing: border-box; }
  html, body {
    width: 1200px;
    height: 831px;
    overflow: hidden;
    background: var(--page);
  }
  .canvas {
    position: relative;
    width: 1200px;
    height: 831px;
  }
  .print {
    position: absolute;
    left: 304px;
    top: 20px;
    width: 591px;
    height: 791px;
    background: var(--paper);
  }
  .date {
    position: absolute;
    left: 0;
    width: 100%;
    text-align: center;
    font-family: "Young Serif", Georgia, serif;
    font-size: 60px;
    line-height: 1;
    color: var(--ink);
    transform: translateY(-50%);
    letter-spacing: 0.5px;
  }
  .date--first  { top: 124px; }
  .date--second { top: 284px; }
  .date--third  { top: 443px; }
  .date--fourth { top: 674px; }
  .ornament {
    position: absolute;
    left: 50%;
    transform: translate(-50%, -50%);
    background: var(--ornament);
    border-radius: 3px;
  }
  .ornament--small  { top: 207px; width: 87px;  height: 8px; }
  .ornament--medium { top: 366px; width: 136px; height: 10px; }
  .ornament--wide   { top: 534px; width: 285px; height: 12px; }
  .ornament--moon   { top: 598px; width: 34px;  height: 34px; border-radius: 50%; }
</style>
</head>
<body>
  <main class="canvas">
    <section class="print">
      <p class="date date--first">6/13/14</p>
      <div class="ornament ornament--small" role="img" aria-label="Small decorative flourish divider"></div>
      <p class="date date--second">7/15/16</p>
      <div class="ornament ornament--medium" role="img" aria-label="Decorative diamond flourish divider"></div>
      <p class="date date--third">8/17/18</p>
      <div class="ornament ornament--wide" role="img" aria-label="Wide decorative line divider with central knot"></div>
      <div class="ornament ornament--moon" role="img" aria-label="Small crescent moon with stairs emblem"></div>
      <p class="date date--fourth">9/19/20</p>
    </section>
  </main>
</body>
</html>
```